Business card for marketing analytics company

Need a business card for new company. I have a logo already that I want to be built into the card and should use those colours

Company is called steered by tallies
Design must bring steered by tallies to life not be a card that could be for anyone with a logo put on it.

Like the front to be fairly clean and uncluttered bringing the logo out with a suitable design on the back of the card.

The logo represents a compass and business growth so those themes along with numbers, analytics , data are appropriate.
I'm often working with creative industries so also needs to reflect the creative side of analytics rather than be very corporate looking.

Target Market(s)

Ad agency, media agency, consumer goods clients

Industry/Entity Type

Market Research

Contact Information for Business Card

Needs to include name, title, email and phone number

Colors
f78f20
f68d4d
ec1f27

Requirements
Must have
• Must bring steered by tallies to life not be a card that could be for anyone with a logo put on it.
• Logo, Correct colours
• Like a design on the back that relates to company name
• Designs for both sides
Should not have
• Please do not just submit logo and a coloured card.
• It needs to have a design element to it
• No black background
• No clear cards - needs front & back

```html
<!DOCTYPE html>
<html lang="en">
<head>
<meta charset="utf-8">
<title>Steered by Tallies — Business Card</title>
<link rel="stylesheet" href="https://fonts.googleapis.com/css2?family=Mulish:wght@400;500;700&display=swap">
<style>
  :root {
    --page-bg: #e6e6e6;
    --card-front: #f7f7f7;
    --card-front-edge: #eeeeee;
    --brand-red: #a2231f;
    --brand-red-deep: #8f1c19;
    --brand-orange: #e0661f;
    --ink: #3b4048;
    --ink-soft: #4a4f57;
    --ring-faint: #f1e3dc;
    --tally-line: rgba(255, 255, 255, 0.13);
    --tally-accent: rgba(247, 143, 32, 0.35);
    --white: #ffffff;
  }
  * { box-sizing: border-box; margin: 0; padding: 0; }
  html, body { width: 1200px; height: 576px; overflow: hidden; }
  body {
    background: var(--page-bg);
    font-family: "Mulish", Arial, sans-serif;
    position: relative;
  }
  .card {
    position: absolute;
    top: 138px;
    height: 294px;
    border-radius: 13px;
    overflow: hidden;
  }
  .card--front {
    left: 82px;
    width: 484px;
    background: linear-gradient(160deg, var(--white) 0%, var(--card-front) 55%, var(--card-front-edge) 100%);
  }
  .card--back {
    left: 602px;
    width: 480px;
    background: linear-gradient(180deg, var(--brand-red) 0%, var(--brand-red) 55%, var(--brand-red-deep) 100%);
  }
  .decor-ring {
    position: absolute;
    left: 214px;
    top: 2px;
    width: 288px;
    height: 288px;
    border: 4px solid var(--ring-faint);
    border-radius: 50%;
  }
  .tally-field {
    position: absolute;
    left: 0;
    top: 0;
    width: 480px;
    height: 294px;
  }
  .tally-field .tally { stroke: var(--tally-line); stroke-width: 3; stroke-linecap: round; fill: none; }
  .tally-field .trend { stroke: var(--tally-accent); stroke-width: 2.5; stroke-linecap: round; stroke-linejoin: round; fill: none; }
  .tally-field .trend-dot { fill: var(--tally-accent); }
  .holder {
    position: absolute;
    left: 29px;
    top: 34px;
  }
  .holder__name {
    font-weight: 700;
    font-size: 18px;
    color: var(--brand-red);
    letter-spacing: 0.2px;
  }
  .holder__title {
    font-size: 10.5px;
    color: var(--ink-soft);
    margin-top: 3px;
  }
  .contact {
    position: absolute;
    left: 29px;
    top: 86px;
    list-style: none;
    font-size: 11.5px;
    line-height: 16.5px;
    color: var(--ink-soft);
  }
  .brand {
    position: absolute;
    display: flex;
    align-items: center;
    gap: 16px;
  }
  .brand__mark {
    width: 56px;
    height: 56px;
    border-radius: 50%;
    flex: none;
  }
  .brand__name {
    font-weight: 700;
    font-size: 19px;
    line-height: 22px;
  }
  .card--front .brand { left: 29px; top: 202px; }
  .card--front .brand__mark { border: 2.5px solid var(--brand-orange); }
  .card--front .brand__name { color: var(--brand-orange); }
  .card--back .brand { left: 248px; top: 198px; }
  .card--back .brand__mark { border: 2.5px solid var(--white); }
  .card--back .brand__name { color: var(--white); }
</style>
</head>
<body>
  <section class="card card--front" aria-label="Card front">
    <div class="decor-ring" aria-hidden="true"></div>
    <div class="holder">
      <p class="holder__name">Paul R. Hale</p>
      <p class="holder__title">Managing Director</p>
    </div>
    <ul class="contact">
      <li>1300 481 592</li>
      <li>www.steeredtallies.com</li>
      <li>hello@steeredtallies.com</li>
    </ul>
    <div class="brand">
      <span class="brand__mark" aria-hidden="true"></span>
      <p class="brand__name">Steered by<br>Tallies</p>
    </div>
  </section>

  <section class="card card--back" aria-label="Card back">
    <svg class="tally-field" viewBox="0 0 480 294" aria-hidden="true">
      <g class="tally">
        <path d="M40 140 V176 M50 140 V176 M60 140 V176 M70 140 V176 M34 170 L76 146"/>
        <path d="M100 118 V154 M110 118 V154 M120 118 V154 M130 118 V154 M94 148 L136 124"/>
        <path d="M160 92 V128 M170 92 V128 M180 92 V128 M190 92 V128 M154 122 L196 98"/>
        <path d="M220 64 V100 M230 64 V100 M240 64 V100 M250 64 V100 M214 94 L256 70"/>
        <path d="M280 38 V74 M290 38 V74 M300 38 V74 M310 38 V74 M274 68 L316 44"/>
      </g>
      <polyline class="trend" points="30,210 55,196 85,202 115,176 145,182 175,150 205,156 235,122 265,128 300,92 330,98 370,56"/>
      <circle class="trend-dot" cx="370" cy="56" r="4"/>
    </svg>
    <div class="brand">
      <span class="brand__mark" aria-hidden="true"></span>
      <p class="brand__name">Steered by<br>Tallies</p>
    </div>
  </section>
</body>
</html>
```